Local fast-growing company in the service sector

We are looking for a modern business card design, which should also appear on our letterheads

Target Market(s)

Private and industrial sectors

Contact Information for Business Card

Vorname Name
Kellberger Str. 18
72815 Lindenau
Tel.: 07146-839214-0
Name@agentur-kvtl.de

Colors
9d9d9d
919191
aaaaaa

Requirements
Must have
• The logo (file) in silver

```html
<!DOCTYPE html>
<html lang="de">
<head>
<meta charset="utf-8">
<title>KVTL – Visitenkarte</title>
<link rel="stylesheet" href="https://fonts.googleapis.com/css2?family=Open+Sans:wght@400;600;700&display=swap">
<style>
  :root {
    --stage: #3a3430;
    --card: #141414;
    --card-edge: #1f1f1f;
    --silver: #aaaaaa;
    --silver-mid: #9d9d9d;
    --silver-dark: #919191;
    --text-light: #e4e4e4;
  }
  * { box-sizing: border-box; margin: 0; padding: 0; }
  html, body {
    width: 1200px; height: 864px; overflow: hidden;
    background: var(--stage);
    font-family: "Open Sans", Arial, sans-serif;
  }
  .canvas {
    width: 1200px; height: 864px;
    display: flex; align-items: center; justify-content: center; gap: 44px;
  }
  .card {
    width: 540px; height: 310px;
    background: var(--card);
    border: 1px solid var(--card-edge);
    border-radius: 3px;
    box-shadow: 0 14px 30px rgba(0,0,0,.45);
    position: relative;
  }
  /* Front */
  .card--front {
    display: flex; flex-direction: column; align-items: center; justify-content: center; gap: 34px;
  }
  .brand {
    display: flex; align-items: center; gap: 12px;
    color: var(--silver); font-weight: 700; letter-spacing: 2px;
  }
  .brand__dot { border-radius: 50%; background: var(--silver-dark); flex: none; }
  .card--front .brand { font-size: 64px; }
  .card--front .brand__dot { width: 26px; height: 26px; }
  .front__web {
    color: var(--silver-dark); font-size: 14px; letter-spacing: 6px;
  }
  /* Back */
  .card--back {
    display: flex; align-items: center; padding: 0 30px 0 40px;
  }
  .card--back .brand { font-size: 42px; width: 230px; }
  .card--back .brand__dot { width: 18px; height: 18px; }
  .divider {
    width: 1px; height: 150px; margin: 0 26px 0 8px; flex: none;
    background: linear-gradient(to bottom, transparent, var(--silver-mid), transparent);
  }
  .contact { color: var(--text-light); font-size: 14px; line-height: 1.5; white-space: nowrap; }
  .contact__name {
    color: var(--silver-mid); font-weight: 700; font-size: 14px; letter-spacing: .5px;
    text-transform: uppercase; margin-bottom: 10px;
  }
  .contact__row { display: flex; align-items: center; gap: 8px; }
  .contact__row svg { width: 11px; height: 11px; flex: none; fill: var(--silver); }
  .contact__address { margin-bottom: 2px; }
</style>
</head>
<body>
<main class="canvas">
  <section class="card card--front" aria-label="Vorderseite">
    <div class="brand"><span class="brand__dot"></span><span>KVTL</span></div>
    <p class="front__web">www.agentur-kvtl.de</p>
  </section>

  <section class="card card--back" aria-label="Rückseite">
    <div class="brand"><span class="brand__dot"></span><span>KVTL</span></div>
    <div class="divider"></div>
    <div class="contact">
      <p class="contact__name">Jonas Keller</p>
      <p class="contact__address">Kellberger Str. 18<br>72815 Lindenau</p>
      <p class="contact__row">
        <svg viewBox="0 0 12 12"><path d="M3 1l2 2.5-1.2 1.3a7 7 0 0 0 3.4 3.4L8.5 7 11 9l-1.3 2C5 11 1 7 1 2.3z"/></svg>
        07146-839214-0
      </p>
      <p class="contact__row">
        <svg viewBox="0 0 12 12"><path d="M1 3h10v6H1z"/><path d="M1 3l5 3.5L11 3" fill="none" stroke="#141414" stroke-width="1"/></svg>
        Name@agentur-kvtl.de
      </p>
      <p class="contact__row">
        <svg viewBox="0 0 12 12"><circle cx="6" cy="6" r="5"/><path d="M1 6h10M6 1c2.2 2.8 2.2 7.2 0 10M6 1c-2.2 2.8-2.2 7.2 0 10" fill="none" stroke="#141414" stroke-width=".9"/></svg>
        www.agentur-kvtl.de
      </p>
    </div>
  </section>
</main>
</body>
</html>
```